U.S. Popcorn company needs business cards

We are a popcorn company that manufactures popcorn and sells it to grocery stores worldwide. Our theme is "Americana" and our logo is U.S. route 66 which is the most famous highway in the U.S.

We would like the design to be simple and to use both sides. On the back side we would like to see just the logo and website. The front would be normal details

Target Market(s)

Wholesalers, grocers and distributors

Industry/Entity Type

Manufacture

Contact Information for Business Card

Business name: Prairie Lantern Popcorn
Phone: +1 555 308 4726
Email: Dale@prairielanternpopcorn.com
website: www.prairielanternpopcorn.com
Tag Line: "POPped fresh every day"
Name: Dale Whitcombe
Title: Founder/President

Requirements
Must have
• Either this design should be fun or clean and simple. I will let you show me your thougths.
Nice to have
• Anything that ties in the real Hwy Route 66.
• Colors might need to be red, white and blue incorporated.
Should not have
• Not be too busy.

```html
<!DOCTYPE html>
<html lang="en">
<head>
<meta charset="utf-8">
<title>Prairie Lantern Popcorn — Business Cards</title>
<link rel="stylesheet" href="https://fonts.googleapis.com/css2?family=Mulish:ital,wght@0,400;0,600;0,800;1,400&display=swap">
<style>
  :root {
    --navy: #14306b;
    --red: #d9201f;
    --white: #ffffff;
    --paper: #e4e4e4;
    --ink: #1c2f63;
  }
  * { box-sizing: border-box; margin: 0; padding: 0; }
  html, body {
    width: 1200px; height: 576px; overflow: hidden;
    background: var(--paper);
    font-family: "Mulish", sans-serif;
  }
  .stage { position: relative; width: 1200px; height: 576px; }
  .card {
    position: absolute; top: 138px;
    width: 484px; height: 294px;
    background: var(--white);
    border-radius: 6px;
    overflow: hidden;
  }
  .card--back { left: 82px; }
  .card--front { left: 602px; width: 482px; height: 292px; }

  /* Back side */
  .back-name {
    position: absolute; left: 0; right: 0; top: 104px;
    text-align: center;
    color: var(--navy);
    font-weight: 800; font-size: 30px; line-height: 1.1;
  }
  .back-web {
    position: absolute; left: 0; right: 0; top: 257px;
    display: flex; align-items: center; justify-content: center; gap: 10px;
    font-size: 11.5px; font-weight: 600; color: var(--navy);
    white-space: nowrap;
  }
  .back-web .rule { width: 44px; height: 2px; background: var(--navy); border-radius: 1px; }
  .accent { color: var(--red); }

  /* Front side */
  .panel { position: absolute; inset: 0; }
  .front-name {
    position: absolute; left: 30px; width: 160px; top: 120px;
    text-align: center;
    color: var(--white);
    font-weight: 800; font-size: 22px; line-height: 1.15;
  }
  .holder {
    position: absolute; right: 24px; top: 27px; text-align: right;
  }
  .holder-name { color: var(--red); font-weight: 800; font-size: 16.5px; }
  .holder-title { color: var(--ink); font-style: italic; font-size: 12px; margin-top: 2px; }
  .contacts {
    position: absolute; right: 24px; top: 184px;
    list-style: none; text-align: right;
    color: var(--ink); font-size: 12.5px; line-height: 18px;
    white-space: nowrap;
  }
  .contacts li { display: flex; justify-content: flex-end; align-items: center; gap: 5px; }
  .contacts svg { width: 11px; height: 11px; fill: var(--red); }
  .tagline {
    position: absolute; right: 24px; top: 244px;
    color: var(--ink); font-size: 15px; white-space: nowrap;
  }
  .tagline strong { color: var(--red); font-weight: 800; }
</style>
</head>
<body>
<main class="stage">

  <section class="card card--back" aria-label="Card back">
    <p class="back-name">Prairie Lantern<br>Popcorn</p>
    <p class="back-web">
      <span class="rule"></span>
      <span>www.<span class="accent">prairielanternpopcorn</span>.com</span>
      <span class="rule"></span>
    </p>
  </section>

  <section class="card card--front" aria-label="Card front">
    <svg class="panel" viewBox="0 0 482 292" width="482" height="292" aria-hidden="true">
      <path d="M0 0 H178 C218 60 228 120 214 180 C206 225 196 260 198 292 H0 Z" fill="var(--navy)"/>
      <path d="M178 0 H194 C236 60 244 130 230 190 C220 232 206 262 204 292 H198 C196 260 206 225 214 180 C228 120 218 60 178 0 Z" fill="var(--red)"/>
    </svg>
    <p class="front-name">Prairie Lantern<br>Popcorn</p>

    <div class="holder">
      <p class="holder-name">Dale Whitcombe</p>
      <p class="holder-title">Founder/President</p>
    </div>

    <ul class="contacts">
      <li>+1 555 308 4726
        <svg viewBox="0 0 24 24"><path d="M6.6 10.8a15 15 0 0 0 6.6 6.6l2.2-2.2a1 1 0 0 1 1-.25 11.4 11.4 0 0 0 3.6.57 1 1 0 0 1 1 1V20a1 1 0 0 1-1 1A17 17 0 0 1 3 4a1 1 0 0 1 1-1h3.5a1 1 0 0 1 1 1c0 1.25.2 2.45.57 3.57a1 1 0 0 1-.25 1z"/></svg>
      </li>
      <li>Dale@prairielanternpopcorn.com
        <svg viewBox="0 0 24 24"><path d="M2 5h20v14H2z M4 7v.5l8 5 8-5V7l-8 5z" fill-rule="evenodd"/></svg>
      </li>
      <li><span>www.<span class="accent">prairielanternpopcorn</span>.com</span>
        <svg viewBox="0 0 24 24"><path d="M12 2a10 10 0 1 0 0 20 10 10 0 0 0 0-20zm-1 3v5H7.1A8 8 0 0 1 11 5zm2 0a8 8 0 0 1 3.9 5H13zm-8 7h6v7a8 8 0 0 1-6-7zm8 0h6a8 8 0 0 1-6 7z"/></svg>
      </li>
    </ul>

    <p class="tagline">"<strong>POP</strong>ped fresh every day"</p>
  </section>

</main>
</body>
</html>
```